General contractor/GM consaltant business card

I need a card for my contracting company in North Dakota, we build industrial buildings for the oil feild and oil feild related companies offices, shops, airplain hangars, airports ext. We have a familly atmosphere on the job and are very relational and personal.
Industry/Entity Type
Industrial
Contact Information for Business Card
Ridgepost Contractors LLC.
Derek T.Holloway
4837 Tamarind dr. Colorado Springs, CO. 80917
Cell# 406-555-0148
derek@ridgepostcontractors.com

```html
<!DOCTYPE html>
<html lang="en">
<head>
<meta charset="utf-8">
<title>Ridgepost Contractors LLC. — Business Card</title>
<link rel="stylesheet" href="https://fonts.googleapis.com/css2?family=Michroma&family=Arimo:wght@400;700&family=Italiana&display=swap">
<style>
  :root {
    --backdrop: #dfe3e4;
    --card-front: #eef0fa;
    --card-back: #dbe4f7;
    --ink: #1b1b1f;
    --ink-soft: #3a3d46;
    --mark-faint: rgba(150, 160, 185, 0.16);
    --card-shadow: 0 14px 30px rgba(60, 70, 80, 0.18);
  }
  * { margin: 0; padding: 0; box-sizing: border-box; }
  html, body {
    width: 1200px;
    height: 1200px;
    overflow: hidden;
    background: var(--backdrop);
  }
  .canvas {
    width: 1200px;
    height: 1200px;
    display: flex;
    flex-direction: column;
    align-items: center;
    justify-content: center;
    gap: 56px;
  }
  .card {
    position: relative;
    width: 900px;
    height: 514px;
    overflow: hidden;
    box-shadow: var(--card-shadow);
  }

  /* Front */
  .card--front { background: var(--card-front); }
  .front-deco {
    position: absolute;
    left: -60px;
    top: 200px;
    width: 520px;
    height: 360px;
  }
  .wordmark {
    position: absolute;
    left: 300px;
    top: 70px;
    font-family: "Michroma", sans-serif;
    font-size: 34px;
    font-weight: 400;
    line-height: 1.32;
    letter-spacing: 3px;
    text-transform: uppercase;
    color: var(--ink);
  }

  /* Back */
  .card--back { background: var(--card-back); }
  .back-deco {
    position: absolute;
    right: -70px;
    top: 60px;
    width: 300px;
    height: 330px;
  }
  .holder-name {
    position: absolute;
    left: 330px;
    top: 150px;
    font-family: "Italiana", serif;
    font-size: 30px;
    line-height: 1.2;
    letter-spacing: 1px;
    color: var(--ink-soft);
    white-space: nowrap;
  }
  .contact {
    position: absolute;
    font-family: "Arimo", Arial, sans-serif;
    font-size: 15px;
    line-height: 1.5;
    color: var(--ink-soft);
    display: grid;
    grid-template-columns: auto auto;
    column-gap: 24px;
  }
  .contact dt { font-weight: 700; letter-spacing: 0.5px; }
  .contact dd { margin: 0; }
  .contact--personal { left: 56px; bottom: 58px; }
  .contact--company { left: 545px; top: 240px; column-gap: 12px; }
</style>
</head>
<body>
<main class="canvas">
  <section class="card card--front" aria-label="Card front">
    <svg class="front-deco" viewBox="0 0 520 360" aria-hidden="true">
      <rect x="40" y="20" width="360" height="320" rx="40" fill="var(--mark-faint)"/>
    </svg>
    <h1 class="wordmark">Ridgepost<br>Contractors LLC.</h1>
  </section>

  <section class="card card--back" aria-label="Card back">
    <svg class="back-deco" viewBox="0 0 300 330" aria-hidden="true">
      <rect x="20" y="20" width="280" height="290" rx="36" fill="var(--mark-faint)"/>
    </svg>
    <p class="holder-name">Derek T.Holloway</p>

    <dl class="contact contact--company">
      <dt>Web:</dt><dd>www.ridgepostcontractors.com</dd>
      <dt>Address:</dt><dd>4837 Tamarind dr. Colorado<br>Springs, CO. 80917</dd>
    </dl>

    <dl class="contact contact--personal">
      <dt>Cell:</dt><dd>406-555-0148</dd>
      <dt>Email:</dt><dd>derek@ridgepostcontractors.com</dd>
    </dl>
  </section>
</main>
</body>
</html>
```